Internal web page of multinational company - Portfolio of reports

We need to improve the look & feel of an existing internal HTML page.
We use it as a portfolios where users go and see a list of existing reports as "tiles". The HTML page is automatically generated by a javascript that reads the contents to display from an HTML file.
What is needs is a "face lift" in the design of the page.
Currently we use icons on the top right of each tile to denote the type of technology used on the report and also colons for the same purpose. The attached screenshots will be self explanatory.
Across the top we have "tabs" that, once selected change the tiles.
Need a proposal for new design that keeps is as clean as possible, specially the home page that should be very light (Plimbo like).
The idea for this page is to serve as a "one stop shop" and become a bookmark for everyone in the company.
Looking for a wow effect that make is visually

Target Market(s)

Internal employees

Industry/Entity Type

It Company

Coding

Coded - Design and coding required

Number of Pages Required

2 page

Requirements
Must have
• Should not change the logo or its position from the bottom left.
• Page must be as clean as possible and
Nice to have
• Welcome to change the logo on the top left. This page is from the CSU M&I (Mni) which stands for Central Support Unit - Metrics & Insight.
Should not have
• Do no use red, this is the color of our competitor. The blue on the bottom is standard for our logo

```html
<!DOCTYPE html>
<html lang="en">
<head>
<meta charset="utf-8">
<title>Report Portfolio – Finance</title>
<link rel="stylesheet" href="https://fonts.googleapis.com/css2?family=Raleway:wght@400;500;600&family=Roboto+Condensed:wght@400;700&family=Open+Sans:wght@400&display=swap">
<style>
  :root {
    --page-bg: #efefef;
    --header-bg: #ffffff;
    --brand-navy: #1b3a86;
    --nav-text: #2c4a98;
    --nav-muted: #8a8a8a;
    --nav-highlight: #e6e6e6;
    --tile-bg: #ffffff;
    --tile-border: #dedede;
    --tile-title: #2c4a98;
    --tile-mark: #d6d6d6;
    --icon-tool: #2c4a98;
    --icon-doc: #3aa6e8;
    --icon-chart: #f5a300;
    --orange-top: #fbb400;
    --orange-bottom: #f47e00;
    --sky-top: #5cc6f6;
    --sky-bottom: #2a9ae8;
    --footer-bg: #0c4a9c;
    --footer-text: #e8eefb;
    --search-border: #d2d2d2;
    --search-text: #666666;
  }
  * { box-sizing: border-box; margin: 0; padding: 0; }
  html, body { width: 1200px; height: 669px; overflow: hidden; }
  body { position: relative; background: var(--page-bg); font-family: "Raleway", sans-serif; }

  .site-header {
    position: absolute; left: 0; top: 0; width: 1200px; height: 76px;
    background: var(--header-bg); border-bottom: 1px solid #dcdcdc;
  }
  .brand { position: absolute; left: 141px; top: 19px; display: flex; align-items: center; gap: 7px; }
  .brand-dot { width: 38px; height: 38px; border-radius: 50%; background: var(--brand-navy); }
  .brand-name { font-family: "Roboto Condensed", sans-serif; font-weight: 700; font-size: 13px; color: var(--brand-navy); letter-spacing: -0.2px; }

  .main-nav { position: absolute; left: 288px; top: 0; height: 76px; display: flex; align-items: center; }
  .nav-item {
    height: 76px; display: flex; align-items: center; padding: 0 6px;
    font-family: "Roboto Condensed", sans-serif; font-weight: 700; font-size: 11.5px;
    color: var(--nav-text); text-decoration: none; white-space: nowrap;
  }
  .nav-item.is-active { background: var(--brand-navy); color: #fff; padding: 0 9px; }
  .nav-item.is-hover { background: var(--nav-highlight); padding: 0 6px 0 6px; width: 134px; }
  .nav-item.is-filter { color: var(--nav-muted); font-weight: 400; }

  .search {
    position: absolute; left: 863px; top: 26px; width: 198px; height: 28px;
    display: flex; border: 1px solid var(--search-border); background: #fff;
  }
  .search-field { flex: 1; font-family: "Open Sans", sans-serif; font-size: 10px; color: var(--search-text); padding: 0 9px; display: flex; align-items: center; }
  .search-btn { width: 30px; border-left: 1px solid var(--search-border); background: #f5f5f5; display: flex; align-items: center; justify-content: center; }

  .tile-grid {
    position: absolute; left: 139px; top: 109px;
    display: grid; grid-template-columns: repeat(4, 224px); grid-auto-rows: 90px;
    column-gap: 9px; row-gap: 13px;
  }
  .tile { position: relative; background: var(--tile-bg); border: 1px solid var(--tile-border); }
  .tile-marks { position: absolute; left: 11px; top: 20px; display: flex; gap: 3px; }
  .mark-box { width: 13px; height: 10px; background: var(--tile-mark); }
  .tile-title {
    position: absolute; left: 46px; top: 17px; right: 10px;
    font-size: 12.5px; font-weight: 500; line-height: 18px; color: var(--tile-title); text-transform: uppercase;
  }
  .tile-tools { position: absolute; right: 10px; bottom: 9px; display: flex; gap: 8px; }
  .tile-tools svg { width: 15px; height: 15px; }
  .ic-tool { color: var(--icon-tool); }
  .ic-doc { color: var(--icon-doc); }
  .ic-chart { color: var(--icon-chart); }
  .tile.is-orange { background: linear-gradient(180deg, var(--orange-top), var(--orange-bottom)); border-color: transparent; }
  .tile.is-sky { background: linear-gradient(180deg, var(--sky-top), var(--sky-bottom)); border-color: transparent; }
  .tile.is-orange .tile-title, .tile.is-sky .tile-title { color: #fff; font-weight: 400; }
  .tile.is-orange .mark-box, .tile.is-sky .mark-box,
  .tile.is-orange .tile-tools svg, .tile.is-sky .tile-tools svg { color: #fff; background-color: transparent; }
  .tile.is-orange .mark-box, .tile.is-sky .mark-box { background: #fff; }

  .site-footer {
    position: absolute; left: 0; top: 610px; width: 1200px; height: 59px; background: var(--footer-bg);
  }
  .footer-note { position: absolute; left: 142px; top: 22px; font-family: "Open Sans", sans-serif; font-size: 12px; color: var(--footer-text); }
  .footer-social { position: absolute; left: 984px; top: 21px; display: flex; gap: 9px; }
  .social-dot { width: 15px; height: 15px; border-radius: 50%; background: #fff; }
</style>
</head>
<body>
<svg width="0" height="0" style="position:absolute" aria-hidden="true">
  <symbol id="i-mail" viewBox="0 0 16 12"><rect width="16" height="12" fill="currentColor"/><path d="M0 0 L8 6 L16 0" fill="none" stroke="#fff" stroke-width="1.4"/></symbol>
  <symbol id="i-tool" viewBox="0 0 16 16"><path d="M10.5 1a4.5 4.5 0 0 0-4.2 6.1L1 12.4 3.6 15l5.3-5.3A4.5 4.5 0 0 0 15 5.5l-2.7 2.7-2.5-.5-.5-2.5L12 2.5A4.5 4.5 0 0 0 10.5 1z" fill="currentColor"/></symbol>
  <symbol id="i-doc" viewBox="0 0 16 16"><path d="M3 1h7l3 3v11H3z" fill="none" stroke="currentColor" stroke-width="1.4"/><path d="M5.5 7h5M5.5 9.5h5M5.5 12h5" stroke="currentColor" stroke-width="1.2"/></symbol>
  <symbol id="i-chart" viewBox="0 0 16 16"><path d="M1 15h15" stroke="currentColor" stroke-width="1.4"/><rect x="2" y="8" width="2" height="6" fill="currentColor"/><rect x="5.5" y="4" width="2" height="10" fill="currentColor"/><rect x="9" y="6" width="2" height="8" fill="currentColor"/><rect x="12.5" y="2" width="2" height="12" fill="currentColor"/></symbol>
</svg>

<header class="site-header">
  <div class="brand"><span class="brand-dot"></span><span class="brand-name">Tilebase Portfolio</span></div>
  <nav class="main-nav">
    <a class="nav-item is-active">FINANCE</a>
    <a class="nav-item">GM VIEW</a>
    <a class="nav-item">HUB VIEW</a>
    <a class="nav-item">MI</a>
    <a class="nav-item is-hover">GENERAL ACCOUNTING</a>
    <a class="nav-item">TAX</a>
    <a class="nav-item">TREASURY</a>
    <a class="nav-item">KNOWLEDGE</a>
    <a class="nav-item is-filter">FILTER</a>
  </nav>
  <div class="search">
    <div class="search-field">Search here</div>
    <div class="search-btn"><svg width="13" height="13" viewBox="0 0 14 14"><circle cx="6" cy="6" r="4.5" fill="none" stroke="#9a9a9a" stroke-width="1.8"/><path d="M9.3 9.3l3.6 3.6" stroke="#9a9a9a" stroke-width="2"/></svg></div>
    <div class="search-btn"><svg width="9" height="9" viewBox="0 0 10 10"><path d="M1 1l8 8M9 1l-8 8" stroke="#9a9a9a" stroke-width="1.5"/></svg></div>
  </div>
</header>

<main class="tile-grid">
  <article class="tile"><div class="tile-marks"><span class="mark-box"></span><svg width="15" height="11" style="color:var(--tile-mark)"><use href="#i-mail"/></svg></div><h2 class="tile-title">B&amp;AT Revenue &amp;<br>Margin Analysis</h2><div class="tile-tools"><svg class="ic-tool"><use href="#i-tool"/></svg><svg class="ic-doc"><use href="#i-doc"/></svg><svg class="ic-chart"><use href="#i-chart"/></svg></div></article>
  <article class="tile is-orange"><div class="tile-marks"><span class="mark-box"></span><svg width="15" height="11" style="color:#fff"><use href="#i-mail"/></svg></div><h2 class="tile-title">Bolt</h2><div class="tile-tools"><svg><use href="#i-tool"/></svg><svg><use href="#i-doc"/></svg><svg><use href="#i-chart"/></svg></div></article>
  <article class="tile"><div class="tile-marks"><span class="mark-box"></span><svg width="15" height="11" style="color:var(--tile-mark)"><use href="#i-mail"/></svg></div><h2 class="tile-title">BSQ Dashboard</h2><div class="tile-tools"><svg class="ic-tool"><use href="#i-tool"/></svg><svg class="ic-doc"><use href="#i-doc"/></svg><svg class="ic-chart"><use href="#i-chart"/></svg></div></article>
  <article class="tile"><div class="tile-marks"><span class="mark-box"></span><svg width="15" height="11" style="color:var(--tile-mark)"><use href="#i-mail"/></svg></div><h2 class="tile-title">Global JV Trends</h2><div class="tile-tools"><svg class="ic-tool"><use href="#i-tool"/></svg><svg class="ic-doc"><use href="#i-doc"/></svg><svg class="ic-chart"><use href="#i-chart"/></svg></div></article>

  <article class="tile"><div class="tile-marks"><span class="mark-box"></span><svg width="15" height="11" style="color:var(--tile-mark)"><use href="#i-mail"/></svg></div><h2 class="tile-title">Inventory<br>Reconciliations</h2><div class="tile-tools"><svg class="ic-tool"><use href="#i-tool"/></svg><svg class="ic-doc"><use href="#i-doc"/></svg><svg class="ic-chart"><use href="#i-chart"/></svg></div></article>
  <article class="tile"><div class="tile-marks"><span class="mark-box"></span><svg width="15" height="11" style="color:var(--tile-mark)"><use href="#i-mail"/></svg></div><h2 class="tile-title">Larkin Inventory<br>Indictors</h2><div class="tile-tools"><svg class="ic-tool"><use href="#i-tool"/></svg><svg class="ic-doc"><use href="#i-doc"/></svg><svg class="ic-chart"><use href="#i-chart"/></svg></div></article>
  <article class="tile"><div class="tile-marks"><span class="mark-box"></span><svg width="15" height="11" style="color:var(--tile-mark)"><use href="#i-mail"/></svg></div><h2 class="tile-title">MI BS Metrics</h2><div class="tile-tools"><svg class="ic-tool"><use href="#i-tool"/></svg><svg class="ic-doc"><use href="#i-doc"/></svg><svg class="ic-chart"><use href="#i-chart"/></svg></div></article>
  <article class="tile"><div class="tile-marks"><span class="mark-box"></span><svg width="15" height="11" style="color:var(--tile-mark)"><use href="#i-mail"/></svg></div><h2 class="tile-title">MI Negative Inventory</h2><div class="tile-tools"><svg class="ic-tool"><use href="#i-tool"/></svg><svg class="ic-doc"><use href="#i-doc"/></svg><svg class="ic-chart"><use href="#i-chart"/></svg></div></article>

  <article class="tile"><div class="tile-marks"><span class="mark-box"></span><svg width="15" height="11" style="color:var(--tile-mark)"><use href="#i-mail"/></svg></div><h2 class="tile-title">MI PCPR</h2><div class="tile-tools"><svg class="ic-tool"><use href="#i-tool"/></svg><svg class="ic-doc"><use href="#i-doc"/></svg><svg class="ic-chart"><use href="#i-chart"/></svg></div></article>
  <article class="tile"><div class="tile-marks"><span class="mark-box"></span><svg width="15" height="11" style="color:var(--tile-mark)"><use href="#i-mail"/></svg></div><h2 class="tile-title">MI PO Performance</h2><div class="tile-tools"><svg class="ic-tool"><use href="#i-tool"/></svg><svg class="ic-doc"><use href="#i-doc"/></svg><svg class="ic-chart"><use href="#i-chart"/></svg></div></article>
  <article class="tile is-orange"><div class="tile-marks"><span class="mark-box"></span><svg width="15" height="11" style="color:#fff"><use href="#i-mail"/></svg></div><h2 class="tile-title">NAM Balance Sheet<br>Online Tool</h2><div class="tile-tools"><svg><use href="#i-tool"/></svg><svg><use href="#i-doc"/></svg><svg><use href="#i-chart"/></svg></div></article>
  <article class="tile is-sky"><div class="tile-marks"><span class="mark-box"></span><svg width="15" height="11" style="color:#fff"><use href="#i-mail"/></svg></div><h2 class="tile-title">Reporter- Fiance<br>Consolidated</h2><div class="tile-tools"><svg><use href="#i-tool"/></svg><svg><use href="#i-doc"/></svg><svg><use href="#i-chart"/></svg></div></article>

  <article class="tile is-orange"><div class="tile-marks" style="top:22px"><span class="mark-box"></span><svg width="15" height="11" style="color:#fff"><use href="#i-mail"/></svg></div><h2 class="tile-title" style="top:20px">Sort</h2><div class="tile-tools"><svg><use href="#i-tool"/></svg><svg><use href="#i-doc"/></svg><svg><use href="#i-chart"/></svg></div></article>
  <article class="tile"><div class="tile-marks" style="top:22px"><span class="mark-box"></span><svg width="15" height="11" style="color:var(--tile-mark)"><use href="#i-mail"/></svg></div><h2 class="tile-title" style="top:20px">Sort Utilization</h2><div class="tile-tools"><svg class="ic-tool"><use href="#i-tool"/></svg><svg class="ic-doc"><use href="#i-doc"/></svg><svg class="ic-chart"><use href="#i-chart"/></svg></div></article>
</main>

<footer class="site-footer">
  <p class="footer-note">© 2015 Company Name&nbsp; All right reserved&nbsp; Term of Use</p>
  <div class="footer-social"><span class="social-dot"></span><span class="social-dot"></span><span class="social-dot"></span></div>
</footer>
</body>
</html>
```